Yard sign design for high end luxury home builder.

Need a design for signage on custom homes that are being built. I already have a logo that I am satisfied with that needs to be incorporated. I need the following incorporated in the design of the sign-
- Lic number 381526
- phone number (805) 555-0148‬
- quennbuilderscrew.com
- Logo/Branding

If possible it may be nice to have the following quote that is on are business cards-

Quote from Gerard of Norvelle-
HE WHO WORKS WITH HIS HANDS IS A LABORER.
HE WHO WORKS WITH HIS HANDS & HIS HEAD IS A CRAFTSMAN.
HE WHO WORKS WITH HIS HANDS & HIS HEAD & HIS HEART IS AN ARTISAN.
-GERARD OF NORVELLE

Target Market(s)

Archetect, Designers, Clients desiring to build a new home or remodel.

Colors
fde9d4
fee4d5
fabb94
fac994
faa54b
f68d4d
f37122
f78f20
f68e4e

Requirements
Must have
• - Lic number 381526
• - phone number (805) 555-0148‬
• - quennbuilderscrew.com
• - Logo/Branding
Nice to have
• Quote from Gerard of Norvelle-
• HE WHO WORKS WITH HIS HANDS IS A LABORER.
• HE WHO WORKS WITH HIS HANDS & HIS HEAD IS A CRAFTSMAN.
• HE WHO WORKS WITH HIS HANDS & HIS HEAD & HIS HEART IS AN ARTISAN.
• -GERARD OF NORVELLE
• OR the below statement-
• Homes Built by Hand
Should not have
• Any additional verbiage not specified above including any type of verbiage about what kind of company we are. For instance- Integrity, reputable... It's just all played out. Im just looking for a bitching design that has the info that compliments my logo/branding.

```html
<!DOCTYPE html>
<html lang="en">
<head>
<meta charset="utf-8">
<title>Quenn Builders Crew – Yard Sign</title>
<link rel="stylesheet" href="https://fonts.googleapis.com/css2?family=Montserrat:wght@500;600;700&family=Roboto+Condensed:wght@700&display=swap">
<style>
  :root {
    --backdrop: #e9e7e4;
    --sign-white: #ffffff;
    --brand-brown: #8b7a67;
    --mark-brown: #6e5b49;
    --orange-deep: #f37122;
    --orange-bright: #f78f20;
    --ink: #111111;
    --rule-white: #ffffff;
  }
  * { margin: 0; padding: 0; box-sizing: border-box; }
  html, body {
    width: 1200px;
    height: 1000px;
    overflow: hidden;
    background: var(--backdrop);
  }
  .canvas {
    position: relative;
    width: 1200px;
    height: 1000px;
  }
  .yard-sign {
    position: absolute;
    left: 240px;
    top: 22px;
    width: 720px;
    height: 955px;
    background: var(--sign-white);
    box-shadow: 0 6px 24px rgba(0,0,0,0.12);
    overflow: hidden;
  }
  .brand-block {
    position: absolute;
    top: 70px;
    left: 0;
    width: 100%;
    display: flex;
    flex-direction: column;
    align-items: center;
  }
  .brand-square {
    width: 330px;
    height: 330px;
    background: var(--mark-brown);
  }
  .brand-name {
    margin-top: 28px;
    font-family: "Montserrat", sans-serif;
    font-weight: 700;
    color: var(--brand-brown);
    text-align: center;
    line-height: 1;
  }
  .brand-name .name-main {
    display: block;
    font-size: 72px;
    letter-spacing: 6px;
  }
  .brand-name .name-sub {
    display: block;
    margin-top: 10px;
    font-size: 27px;
    letter-spacing: 2px;
  }
  .phone-band {
    position: absolute;
    top: 600px;
    left: 0;
    width: 100%;
    height: 165px;
    background: linear-gradient(180deg, var(--orange-deep), var(--orange-bright));
    display: flex;
    align-items: center;
    justify-content: center;
  }
  .phone-band::before,
  .phone-band::after {
    content: "";
    position: absolute;
    left: 0;
    width: 100%;
    height: 3px;
    background: var(--rule-white);
  }
  .phone-band::before { top: 12px; }
  .phone-band::after { bottom: 12px; }
  .phone-number {
    font-family: "Roboto Condensed", sans-serif;
    font-weight: 700;
    font-size: 94px;
    color: var(--sign-white);
    letter-spacing: 1px;
  }
  .contact-details {
    position: absolute;
    top: 785px;
    left: 0;
    width: 100%;
    text-align: center;
    font-family: "Montserrat", sans-serif;
    color: var(--ink);
  }
  .website {
    font-weight: 600;
    font-size: 33px;
  }
  .license {
    margin-top: 10px;
    font-weight: 500;
    font-size: 22px;
    letter-spacing: 1px;
  }
  .tagline-tab {
    position: absolute;
    left: 132px;
    bottom: 0;
    width: 476px;
    height: 76px;
    background: linear-gradient(90deg, var(--orange-deep), var(--orange-bright));
    clip-path: polygon(5% 0, 95% 0, 100% 100%, 0 100%);
    display: flex;
    align-items: center;
    justify-content: center;
  }
  .tagline {
    font-family: "Montserrat", sans-serif;
    font-weight: 600;
    font-size: 29px;
    color: var(--sign-white);
  }
</style>
</head>
<body>
  <main class="canvas">
    <section class="yard-sign">
      <header class="brand-block">
        <div class="brand-square"></div>
        <h1 class="brand-name">
          <span class="name-main">QUENN</span>
          <span class="name-sub">BUILDERS CREW</span>
        </h1>
      </header>

      <div class="phone-band">
        <p class="phone-number">(805) 555-0148</p>
      </div>

      <div class="contact-details">
        <p class="website">www.quennbuilderscrew.com</p>
        <p class="license">LIC NUMBER 381526</p>
      </div>

      <div class="tagline-tab">
        <p class="tagline">Homes Built by Hand</p>
      </div>
    </section>
  </main>
</body>
</html>
```